Reginald's Book Cover

Need a cover design for a book (paperback and eBook)
Book Title: Songs From The Old Trapline
Book Width: 15.24
Book Height: 22.86
Thickness: approximately 200 pages.
Book is a collection of stories drawn from the author's life, and will be in the local history genre in northern British Columbia, Canada from the period 1930 to the present time.
Author: Reginald Hugh Pettigrew
Must include "As told to Wendy Falkner" on front cover, not on the spine.
Author invites designers creativity and asks that the attached photos be incorporated into the front and back covers in tasteful ways as follows:
- Back Cover_Reginald_Marta_Knobby – goes on back cover
- Back Cover_Grizzly - goes on the back cover
- Front Cover_Mountain Flowers - goes on the front cover
- Front Cover_Reginald_in Alpine - goes on the front cover
Other uses of the photos will be considered.
We apologize for the quality of the photos. Please do what you can.
We look forward to your designs.
Thank you for considering.

Target Market(s)

Lovers of local history, jokes, storytelling, back country hiking and mountain climbing. Men and women 30 years and older. Primary target readership are men and women in their 40's, 50's, 60's, and older, who love local history

Font styles to use
Sans Serif

Requirements
Must have
• Back cover copy must clear and easy to read.
Must appeal to outdoor, back country types.
Nice to have
• Like to see a creative incorporation of the photos provided.
Build on or compliment the colours in the photos

```html
<!DOCTYPE html>
<html lang="en">
<head>
<meta charset="utf-8">
<title>Songs From The Old Trapline – Cover Spread</title>
<link rel="stylesheet" href="https://fonts.googleapis.com/css2?family=Oswald:wght@400;500;600&family=Tinos&display=swap">
<style>
  :root {
    --paper: #ffffff;
    --ink: #111111;
    --title-blue-dark: #2d6590;
    --title-blue-light: #6a9cc6;
    --sky: #a9bdd6;
    --snow: #e8e6df;
    --meadow: #b8a24a;
    --meadow-deep: #7d7a33;
    --grass: #5f7a3a;
    --grass-deep: #3e4f25;
    --slope: #8a7f55;
    --jacket: #4a6f9e;
  }
  * { margin: 0; padding: 0; box-sizing: border-box; }
  html, body { width: 1200px; height: 862px; overflow: hidden; background: var(--paper); }
  .spread { position: relative; width: 1200px; height: 862px; background: var(--paper); }

  /* Back cover */
  .back { position: absolute; left: 0; top: 0; width: 571px; height: 862px; }
  .back-photo-couple {
    position: absolute; left: 0; top: 0; width: 320px; height: 318px;
    background: linear-gradient(180deg, var(--grass) 0%, var(--jacket) 45%, #4f5f3e 75%, var(--paper) 100%);
  }
  .back-photo-grizzly {
    position: absolute; left: 320px; top: 0; width: 251px; height: 318px;
    background: linear-gradient(180deg, #9a7a5c 0%, var(--snow) 40%, #6f7a4d 70%, var(--paper) 100%);
  }
  .back-copy {
    position: absolute; left: 48px; top: 348px; width: 487px;
    font-family: "Tinos", "Times New Roman", serif;
    font-size: 14.2px; line-height: 17.5px; color: var(--ink); text-align: justify;
  }
  .back-copy p + p { margin-top: 17.5px; }

  /* Spine */
  .spine { position: absolute; left: 571px; top: 0; width: 58px; height: 862px; background: var(--paper); }
  .spine-text {
    position: absolute; left: 50%; writing-mode: vertical-rl;
    transform: translateX(-50%);
    font-family: "Oswald", "Arial Narrow", sans-serif; font-weight: 500;
    font-size: 30px; line-height: 1; letter-spacing: 0.2px; white-space: nowrap;
  }
  .spine-title { top: 50px; color: var(--title-blue-dark); }
  .spine-author { top: 525px; color: var(--ink); }

  /* Front cover */
  .front { position: absolute; left: 629px; top: 0; width: 571px; height: 862px; }
  .front-photo-flowers {
    position: absolute; left: 0; top: 0; width: 571px; height: 322px;
    background: linear-gradient(180deg, var(--sky) 0%, #cdd3da 20%, var(--snow) 30%, var(--meadow) 55%, var(--meadow-deep) 85%, var(--paper) 100%);
  }
  .front-photo-hiker {
    position: absolute; left: 0; top: 540px; width: 571px; height: 322px;
    background: linear-gradient(180deg, var(--paper) 0%, var(--grass) 14%, var(--slope) 55%, var(--grass-deep) 100%);
  }
  .front-title {
    position: absolute; left: 0; top: 348px; width: 571px; text-align: center;
    font-family: "Oswald", "Arial Narrow", sans-serif; font-weight: 600;
    text-transform: uppercase; line-height: 1;
    background: linear-gradient(180deg, var(--title-blue-dark) 0%, var(--title-blue-light) 100%);
    -webkit-background-clip: text; background-clip: text; color: transparent;
  }
  .front-title .line-small { display: block; font-size: 50px; letter-spacing: 0.5px; }
  .front-title .line-large { display: block; font-size: 76px; margin-top: 4px; letter-spacing: 0.5px; }
  .front-credit {
    position: absolute; left: 0; top: 480px; width: 571px; text-align: center;
    font-family: "Oswald", "Arial Narrow", sans-serif; font-weight: 400;
    font-size: 28px; color: var(--ink);
  }
  .front-author {
    position: absolute; left: 0; top: 780px; width: 571px; text-align: center;
    font-family: "Oswald", "Arial Narrow", sans-serif; font-weight: 500;
    font-size: 40px; color: var(--paper); letter-spacing: 0.3px; text-transform: uppercase;
  }
</style>
</head>
<body>
<div class="spread">
  <section class="back">
    <div class="back-photo-couple" role="img" aria-label="Photo of the author and his companion smiling on a green alpine slope"></div>
    <div class="back-photo-grizzly" role="img" aria-label="Photo of a grizzly bear standing on a snowy mountain meadow"></div>
    <div class="back-copy">
      <p>Reginald Pettigrew is a true old-fashioned story teller. He loves nothing better than a good story, and particularly when he is the one telling the story. He was born and raised in the tiny sawmill town of Tamrack, BC and spent 80 years of his life there before relocating to his current home on the banks of the Nechako River in Prince George, BC. In addition to writing this book, Reginald spends his time writing songs, singing, telling jokes, and entertaining his many friends with stories of days gone by.</p>
      <p>At the age of 15 he started his career as a flunky in the cookhouse, then moved on to work as a horse logger, sawmill worker, bush foreman, rancher, cat skinner, forest warden, road and bridge builder, and finished his career as salmon hatchery manager.</p>
      <p>Reginald’s love of the mountains is evident throughout the book, as is his love for the majestic grizzly bears who inhabit them. He spent his spare time mountain climbing, fishing, skiing, snowshoeing, and hiking in the woods near his home. This book is an eclectic collection of stories about family, friends, and adventures, all sprinkled with the author’s unique sense of humour.</p>
    </div>
  </section>

  <section class="spine">
    <span class="spine-text spine-title">SONGS FROM THE OLD TRAPLINE</span>
    <span class="spine-text spine-author">REGINALD HUGH PETTIGREW</span>
  </section>

  <section class="front">
    <div class="front-photo-flowers" role="img" aria-label="Photo of an alpine meadow of yellow wildflowers below snow-patched peaks"></div>
    <h1 class="front-title">
      <span class="line-small">Songs From The</span>
      <span class="line-large">Old Trapline</span>
    </h1>
    <p class="front-credit">As told to Wendy Falkner</p>
    <div class="front-photo-hiker" role="img" aria-label="Photo of the author hiking an alpine trail with a pack and rifle"></div>
    <p class="front-author">Reginald Hugh Pettigrew</p>
  </section>
</div>
</body>
</html>
```